Upmarket Dessert Lounge needs a Business Card Design

We are an upmarket dessert lounge needing a business card to match our image.

We want something that is simple yet beautiful, feminine, classy, sophisticated and elegant. We want it to stand out and don't mind if it is bold.

The design should include our logo and colours of red or maroon with gold highlights. We don't mind if black is used.

Marlow & Quince

Target Market(s)

For those who like to indulge or treat themselves and give in to their temptations on good quality desserts.

Industry/Entity Type

Business

Requirements
Must have
• Must include our logo and our name

Marlow & Quince

M & Q

```html
<!DOCTYPE html>
<html lang="en">
<head>
<meta charset="utf-8">
<title>Marlow &amp; Quince — Business Card</title>
<link href="https://fonts.googleapis.com/css2?family=Tinos:wght@400;700&display=swap" rel="stylesheet">
<style>
  :root {
    --maroon: #7b1416;
    --gold: #f6cf8c;
    --peach: #fcd8a6;
    --ink: #4a4a4a;
    --rule: #c9c9c9;
    --card: #ffffff;
    --backdrop: #ecebe8;
  }
  html, body {
    margin: 0;
    padding: 0;
    width: 1200px;
    height: 417px;
    overflow: hidden;
    background: var(--backdrop);
    font-family: "Tinos", "Times New Roman", serif;
  }
  .canvas {
    position: relative;
    width: 1200px;
    height: 417px;
  }
  .card {
    position: absolute;
    top: 61px;
    width: 513px;
    height: 293px;
    background: var(--card);
    border-radius: 16px;
    box-shadow: 0 2px 6px rgba(0,0,0,0.18);
    overflow: hidden;
  }
  .card--front { left: 56px; }
  .card--back { left: 631px; }

  .brand-name {
    position: absolute;
    top: 84px;
    left: 0;
    right: 0;
    text-align: center;
    font-size: 28px;
    font-weight: 400;
    letter-spacing: 1px;
    color: var(--maroon);
    white-space: nowrap;
  }

  .band {
    position: absolute;
    top: 197px;
    left: 0;
    right: 0;
    height: 30px;
  }
  .band__tab {
    position: absolute;
    left: 0;
    top: 0;
    width: 41px;
    height: 30px;
    background: var(--peach);
  }
  .band__bar {
    position: absolute;
    left: 47px;
    right: 0;
    top: 0;
    height: 30px;
    background: var(--maroon);
    color: var(--gold);
    display: flex;
    align-items: center;
    justify-content: center;
  }
  .holder-name {
    font-size: 18px;
    font-weight: 700;
    letter-spacing: 0.3px;
  }
  .holder-title {
    font-size: 14px;
    font-weight: 400;
    margin-left: 5px;
  }
  .web-address {
    font-size: 15px;
    letter-spacing: 3px;
    color: #fff;
  }

  .contacts {
    position: absolute;
    top: 238px;
    left: 0;
    right: 0;
    height: 44px;
    font-size: 13.5px;
    line-height: 20px;
    color: var(--ink);
  }
  .contacts__col {
    position: absolute;
    top: 0;
  }
  .contacts__col--address { left: 53px; }
  .contacts__col--phone { left: 194px; }
  .contacts__col--online { left: 346px; }
  .contacts__divider {
    position: absolute;
    top: 4px;
    width: 1px;
    height: 38px;
    background: var(--rule);
  }
  .contacts__divider--one { left: 182px; }
  .contacts__divider--two { left: 332px; }
  .contact-line {
    display: flex;
    align-items: center;
    white-space: nowrap;
  }
  .contact-icon {
    width: 11px;
    height: 11px;
    margin-right: 7px;
    fill: var(--maroon);
    flex: none;
  }
</style>
</head>
<body>
<main class="canvas">

  <section class="card card--front" aria-label="Business card front">
    <div class="brand-name">MARLOW &amp; QUINCE</div>

    <div class="band">
      <div class="band__tab"></div>
      <div class="band__bar">
        <span class="holder-name">YOUR NAME,</span><span class="holder-title">Title</span>
      </div>
    </div>

    <div class="contacts">
      <div class="contacts__col contacts__col--address">
        <div class="contact-line">00, Complex name</div>
        <div class="contact-line">City, State 000 000</div>
      </div>
      <span class="contacts__divider contacts__divider--one"></span>
      <div class="contacts__col contacts__col--phone">
        <div class="contact-line">
          <svg class="contact-icon" viewBox="0 0 12 12" aria-hidden="true"><path d="M2.5 0.8 4.3 2.9 3.3 4.3C3.9 5.8 5.4 7.5 7.6 8.6L9 7.6 11.2 9.4 10.2 11.1C5.5 11.3 0.6 6.4 0.9 1.8Z"/></svg>
          +2348000451190
        </div>
        <div class="contact-line">
          <svg class="contact-icon" viewBox="0 0 12 12" aria-hidden="true"><path d="M3 0.5h6a1 1 0 0 1 1 1v9a1 1 0 0 1-1 1H3a1 1 0 0 1-1-1v-9a1 1 0 0 1 1-1Zm0.8 1.5v5.5h4.4V2Zm2.2 6.6a0.9 0.9 0 1 0 0 1.8 0.9 0.9 0 0 0 0-1.8Z"/></svg>
          +2348000451190
        </div>
      </div>
      <span class="contacts__divider contacts__divider--two"></span>
      <div class="contacts__col contacts__col--online">
        <div class="contact-line">
          <svg class="contact-icon" viewBox="0 0 12 12" aria-hidden="true"><path d="M1 2.5h10v1L6 6.6 1 3.5Zm0 2.2 5 3.1 5-3.1V9.5H1Z"/></svg>
          hello@marlowquince.com
        </div>
        <div class="contact-line">
          <svg class="contact-icon" viewBox="0 0 12 12" aria-hidden="true"><circle cx="6" cy="6" r="5"/><path d="M1 6h10M6 1c-2 2.7-2 7.3 0 10M6 1c2 2.7 2 7.3 0 10M2 3.5h8M2 8.5h8" stroke="#fff" stroke-width="0.8" fill="none"/></svg>
          www.marlowquince.com
        </div>
      </div>
    </div>
  </section>

  <section class="card card--back" aria-label="Business card back">
    <div class="brand-name">MARLOW &amp; QUINCE</div>

    <div class="band">
      <div class="band__tab"></div>
      <div class="band__bar">
        <span class="web-address">www.marlowquince.com</span>
      </div>
    </div>
  </section>

</main>
</body>
</html>
```